Calvanto Group Real Estate Company business cards

New business card design, we are generally happy with the basic layout of the existing front of business card, (feel free to change) but require a head shot photo on the back side.

http://www.calvanto.com.au/

Attached logos, and existing business card

------------------------------

Target Market(s)

Real estate

Industry/Entity Type

Real Estate

Contact Information for Business Card

Standard size double sided

Font styles to use
Other font styles liked:
• Futura

Requirements
Must have
• Photo head shot on the back side
Nice to have
• yes
Should not have
• No

```html
<!DOCTYPE html>
<html lang="en">
<head>
<meta charset="utf-8">
<title>Calvanto Group business cards</title>
<link href="https://fonts.googleapis.com/css2?family=Jost:wght@400;500&display=swap" rel="stylesheet">
<style>
  :root {
    --page: #e9e7e4;
    --card: #121212;
    --card-edge: #1c1c1c;
    --brand-purple: #4a3a8f;
    --accent-orange: #f0921c;
    --text-light: #f2f2f2;
    --divider: #8a8a8a;
    --silver: #b9b9b9;
  }
  * { box-sizing: border-box; margin: 0; padding: 0; }
  html, body { width: 1200px; height: 814px; overflow: hidden; }
  body {
    background: var(--page);
    font-family: "Jost", "Futura", sans-serif;
    position: relative;
  }
  .card {
    position: absolute;
    top: 242px;
    width: 540px;
    height: 330px;
    background: var(--card);
    border: 1px solid var(--card-edge);
    box-shadow: 0 6px 18px rgba(0,0,0,0.25);
    overflow: hidden;
  }
  .card--front { left: 40px; }
  .card--back { left: 620px; }

  /* front */
  .brand {
    position: absolute;
    left: 0;
    width: 460px;
    top: 82px;
    text-align: center;
    color: var(--brand-purple);
    font-size: 40px;
    font-weight: 500;
    line-height: 1;
    white-space: nowrap;
  }
  .tagline {
    position: absolute;
    left: 0;
    width: 460px;
    top: 150px;
    text-align: center;
    color: var(--brand-purple);
    font-size: 15px;
    font-weight: 500;
    word-spacing: 6px;
  }
  .person {
    position: absolute;
    right: 310px;
    top: 222px;
    text-align: right;
  }
  .person__name { color: var(--brand-purple); font-size: 20px; font-weight: 500; line-height: 1.1; }
  .person__role { color: var(--accent-orange); font-size: 16px; font-weight: 500; line-height: 1.2; }
  .person__company { color: var(--text-light); font-size: 15px; line-height: 1.3; }
  .divider {
    position: absolute;
    left: 243px;
    top: 186px;
    width: 1px;
    height: 110px;
    background: var(--divider);
  }
  .contact {
    position: absolute;
    left: 258px;
    top: 190px;
    list-style: none;
    color: var(--text-light);
    font-size: 14px;
    line-height: 24px;
  }
  .contact li { display: flex; align-items: center; gap: 7px; white-space: nowrap; }
  .contact svg { width: 12px; height: 12px; fill: var(--brand-purple); flex: none; }

  /* back */
  .portrait {
    position: absolute;
    left: 90px;
    top: 40px;
    width: 250px;
    height: 290px;
    background: radial-gradient(ellipse at 50% 30%, #5b5f78 0%, #2c3560 45%, #1a2146 80%, var(--card) 100%);
    border-radius: 120px 120px 0 0;
  }
  .back-mark {
    position: absolute;
    left: 370px;
    top: 60px;
    width: 60px;
    height: 60px;
    background: var(--silver);
  }
  .back-web {
    position: absolute;
    right: 26px;
    top: 146px;
    color: var(--text-light);
    font-size: 11px;
    letter-spacing: 0.5px;
  }
</style>
</head>
<body>
  <section class="card card--front" aria-label="Business card front">
    <p class="brand">Calvanto Group</p>
    <p class="tagline">Buy | Sell | Rent</p>

    <div class="person">
      <p class="person__name">Daniel Tran</p>
      <p class="person__role">Director</p>
      <p class="person__company">Calvanto Group</p>
    </div>

    <div class="divider"></div>

    <ul class="contact">
      <li>ABN: 12 345 678 901</li>
      <li>
        <svg viewBox="0 0 24 24" aria-hidden="true"><path d="M6.6 10.8a15.2 15.2 0 0 0 6.6 6.6l2.2-2.2c.3-.3.7-.4 1-.2 1.1.4 2.3.6 3.6.6.6 0 1 .4 1 1V20c0 .6-.4 1-1 1A17 17 0 0 1 3 4c0-.6.4-1 1-1h3.5c.6 0 1 .4 1 1 0 1.3.2 2.5.6 3.6.1.3 0 .7-.2 1z"/></svg>
        0400 555 218
      </li>
      <li>
        <svg viewBox="0 0 24 24" aria-hidden="true"><path d="M2 5h20v14H2z"/><path d="M2 5l10 8 10-8" fill="none" stroke="#121212" stroke-width="2"/></svg>
        daniel.tran@calvanto.com.au
      </li>
      <li>
        <svg viewBox="0 0 24 24" aria-hidden="true"><circle cx="12" cy="12" r="11"/></svg>
        www.calvanto.com.au
      </li>
    </ul>
  </section>

  <section class="card card--back" aria-label="Business card back">
    <div class="portrait" role="img" aria-label="Head shot photo of the director in a navy suit and blue tie"></div>
    <div class="back-mark" aria-hidden="true"></div>
    <p class="back-web">www.calvanto.com.au</p>
  </section>
</body>
</html>
```